Business card design for a dynamic IT consulting company

We need a business card design for a young firm, specialized in the Telecommunications/Consulting industry. The name of the company is Quindor and Partners Business Consulting Ltd. (Short name: Quindor and Partnes)
Quindor = solve read reverse, so we aim to be uncomplicated and solution-oriented. The small pipe in our logo is also related to the word solve. So we need a new business card design, which is simple, eye catching and something non traditional (I would probably prefer a square shaped design rather than a rectangle, but open for suggestions). Attached our logo.

Target Market(s)

Usually our customers are Tier1 Telecoms providers (Q-Netra, Palorix, etc) and their executives.

Industry/Entity Type

Business

Contact Information for Business Card

Name: Bence Tolnavari
Email: b.tolnavari@quindor.hu
Web: www.quindor.hu
Mobile: +36 30 518 2769
Title: Managing Director

Optional:
Company name: Quindor and Partners Ltd.
Address: 1087 Budapest, Tolvenka str. 28/C, Hungary

Font styles to use
Other font styles liked:
• helveticaneue_medium, Prime Regular are used now.

Colors

Designer to choose colors to be used in the design.

Requirements
Must have
• I would like to have a 2 sided design.
Nice to have
• I thought if we make the logo a bit bigger (without the company name), that could go to the back with the company name below. I though, if the pipe in the logo is somehow touchable on the business card, would be nice and unique.

```html
<!DOCTYPE html>
<html lang="en">
<head>
<meta charset="utf-8">
<title>Quindor and Partners – Business Card</title>
<link rel="stylesheet" href="https://fonts.googleapis.com/css2?family=Oswald:wght@600&family=Work+Sans:wght@400;500&family=Exo+2:wght@500&display=swap">
<style>
  :root {
    --page-bg: #161616;
    --card-bg: #1e1e1e;
    --card-bg-light: #2e2e2e;
    --accent-blue: #1d9ad6;
    --accent-pink: #c0367e;
    --text-light: #f2f2f2;
    --text-silver: #9a9a9a;
    --mark-grey: #3a3a3a;
  }
  * { margin: 0; padding: 0; box-sizing: border-box; }
  html, body {
    width: 1200px; height: 897px; overflow: hidden;
    background: var(--page-bg);
  }
  .canvas { position: relative; width: 1200px; height: 897px; }

  .card {
    position: absolute; left: 304px; width: 594px; height: 338px;
    border-radius: 20px;
    background: radial-gradient(ellipse at 80% 30%, var(--card-bg-light) 0%, var(--card-bg) 60%);
    box-shadow: 0 6px 16px rgba(0,0,0,.55);
  }
  .card--front { top: 92px; }
  .card--back { top: 470px; }

  .person {
    position: absolute; right: 292px; top: 142px; text-align: right;
  }
  .person__name {
    font-family: 'Oswald', sans-serif; font-weight: 600;
    font-size: 31px; line-height: 1; color: var(--accent-blue);
    letter-spacing: .2px;
  }
  .person__title {
    margin-top: 8px;
    font-family: 'Work Sans', sans-serif; font-weight: 400;
    font-size: 14.5px; line-height: 1; color: var(--text-light);
    letter-spacing: .3px;
  }
  .divider {
    position: absolute; left: 326px; top: 142px; width: 2px; height: 56px;
    background: var(--accent-pink);
  }
  .contacts {
    position: absolute; left: 350px; top: 142px; list-style: none;
    font-family: 'Work Sans', sans-serif; font-size: 13.5px; color: var(--text-light);
  }
  .contacts__item {
    display: flex; align-items: center; height: 19px; margin-bottom: 0.5px;
  }
  .contacts__icon { width: 11px; height: 11px; margin-right: 9px; fill: var(--accent-blue); }

  .company {
    position: absolute; left: 0; right: 0; top: 280px; text-align: center;
  }
  .company__name {
    font-family: 'Exo 2', sans-serif; font-weight: 500;
    font-size: 15px; line-height: 1; color: var(--accent-blue);
  }
  .company__address {
    margin-top: 4px;
    font-family: 'Work Sans', sans-serif; font-size: 13px; line-height: 1.1;
    color: var(--text-light); letter-spacing: .4px;
  }

  .brand {
    position: absolute; left: 0; right: 0; top: 146px;
    display: flex; justify-content: center; align-items: center; gap: 14px;
  }
  .brand__square { width: 30px; height: 30px; background: var(--mark-grey); }
  .brand__name {
    font-family: 'Work Sans', sans-serif; font-weight: 500;
    font-size: 38px; line-height: 1; color: var(--text-silver);
  }
  .web-back {
    position: absolute; left: 0; right: 0; top: 297px; text-align: center;
    font-family: 'Work Sans', sans-serif; font-size: 15px;
    letter-spacing: 2.4px; color: var(--text-light);
  }
</style>
</head>
<body>
<main class="canvas">
  <section class="card card--front" aria-label="Business card front">
    <div class="person">
      <h1 class="person__name">BENCE TOLNAVARI</h1>
      <p class="person__title">MANAGING DIRECTOR</p>
    </div>
    <div class="divider"></div>
    <ul class="contacts">
      <li class="contacts__item">
        <svg class="contacts__icon" viewBox="0 0 24 24"><path d="M6.6 10.8a15 15 0 0 0 6.6 6.6l2.2-2.2a1 1 0 0 1 1-.25 11.4 11.4 0 0 0 3.6.57 1 1 0 0 1 1 1V20a1 1 0 0 1-1 1A17 17 0 0 1 3 4a1 1 0 0 1 1-1h3.5a1 1 0 0 1 1 1c0 1.25.2 2.45.57 3.57a1 1 0 0 1-.25 1z"/></svg>
        +36 30 518 2769
      </li>
      <li class="contacts__item">
        <svg class="contacts__icon" viewBox="0 0 24 24"><path d="M2 5h20v14H2z M2 5l10 7 10-7" stroke="#1e1e1e" stroke-width="1.5"/></svg>
        b.tolnavari@quindor.hu
      </li>
      <li class="contacts__item">
        <svg class="contacts__icon" viewBox="0 0 24 24" fill="none" style="fill:none;stroke:var(--accent-blue);stroke-width:2"><circle cx="12" cy="12" r="10"/><ellipse cx="12" cy="12" rx="4.5" ry="10"/><path d="M2 12h20M4 7h16M4 17h16"/></svg>
        www.quindor.hu
      </li>
    </ul>
    <div class="company">
      <p class="company__name">QUINDOR AND PARTNERS LTD:</p>
      <p class="company__address">1087 Budapest, Tolvenka str. 28/C, Hungary</p>
    </div>
  </section>

  <section class="card card--back" aria-label="Business card back">
    <div class="brand">
      <span class="brand__square"></span>
      <span class="brand__name">Quindor &amp; Partners</span>
    </div>
    <p class="web-back">www.quindor.hu</p>
  </section>
</main>
</body>
</html>
```